UI/ UX Design for ERP Software

We need a new UX/UI interface for a ERP software for property managers. Our CMMS / ERP solution is made based on responsive design technologies and is coded in PHP.
The overall UX to be similar to Tev Ulna - easy navigation, intuitive menus.

Industry/Entity Type

Property Management

Number of Pages Required

5+ page

Requirements
Must have
• Round dock buttons
Consistent icons across the application
Enough Spacing between buttons/icons/ menu
Consistent Font
Nice to have
• We would like the UX to allow the users to use the application without /minimum training.
Should not have
• we don't want anything that is classic with respect to UX

```html
<!DOCTYPE html>
<html lang="en">
<head>
<meta charset="utf-8">
<title>Keystead – Active Dashboard</title>
<link href="https://fonts.googleapis.com/css2?family=Lato:wght@400;700;900&display=swap" rel="stylesheet">
<style>
:root{
  --blue:#0a7cff;
  --blue-deep:#0050ff;
  --side-top:#0a8cf5;
  --navy:#2b4a7a;
  --slate:#4f6077;
  --ink:#3c4656;
  --muted:#5f6b7a;
  --sky:#c9e9f9;
  --page:#f2f4f7;
  --grid:#e3e6ea;
  --white:#ffffff;
}
*{box-sizing:border-box;margin:0;padding:0}
html,body{width:1200px;height:1064px;overflow:hidden}
body{font-family:'Lato',sans-serif;background:var(--page);position:relative;color:var(--ink)}
.sidebar{position:absolute;left:0;top:0;width:207px;height:1011px;background:linear-gradient(160deg,var(--side-top),var(--blue-deep) 60%,var(--side-top));}
.brand{position:absolute;left:0;top:0;width:207px;height:110px}
.brand-name{position:absolute;left:30px;top:26px;display:flex;align-items:center;gap:8px;font-weight:900;font-size:30px;color:var(--blue);letter-spacing:-.5px}
.brand-name i{display:block;width:22px;height:22px;background:var(--blue)}
.menu{position:absolute;left:0;top:121px;list-style:none;width:207px}
.menu li{height:33.5px;display:flex;align-items:center;color:var(--white);font-size:13px}
.menu svg{width:12px;height:12px;margin:0 21px 0 16px;fill:var(--white)}
.stats{position:absolute;left:207px;top:0;width:993px;height:97px;background:var(--sky)}
.stat{position:absolute;top:27px;display:flex;align-items:center;gap:12px}
.stat .dock{width:41px;height:41px;border-radius:50%;border:3px solid var(--blue);background:var(--white);display:flex;align-items:center;justify-content:center}
.stat .dock svg{width:18px;height:18px;fill:var(--blue)}
.stat b{display:block;font-size:18px;font-weight:700;color:var(--ink);line-height:20px}
.stat span{display:block;font-size:14px;color:var(--muted);line-height:18px}
.card{position:absolute;left:230px;top:136px;width:946px;height:832px;background:var(--white);border-radius:3px}
.title{position:absolute;left:31px;top:26px;font-size:35px;font-weight:900;color:var(--slate)}
.title em{font-style:normal;color:var(--blue)}
.ranges{position:absolute;left:399px;top:32px;display:flex;gap:8px}
.ranges span{height:28px;width:81px;border:1px solid #d4d8dd;border-radius:2px;font-size:10.5px;display:flex;align-items:center;justify-content:center;color:var(--ink)}
.ranges span.on{background:var(--blue);border-color:var(--blue);color:var(--white);width:79px}
.period{position:absolute;left:30px;top:110px;width:264px;height:39px;background:var(--slate);color:var(--white);font-weight:700;font-size:18px;display:flex;align-items:center;padding-left:18px;gap:8px}
.period svg{width:18px;height:14px}
.chart{position:absolute;left:0;top:0;width:946px;height:832px;font-family:'Lato',sans-serif}
.legend{position:absolute;left:120px;top:720px;width:720px;display:flex;flex-wrap:wrap;row-gap:12px;column-gap:10px;font-size:12px;color:var(--muted)}
.legend span{display:flex;align-items:center;gap:6px}
.legend i{width:9px;height:9px;border-radius:2px;display:block}
.footer{position:absolute;left:0;top:1011px;width:1200px;height:53px;background:var(--slate);color:var(--white);font-size:13px;display:flex;align-items:center;justify-content:center}
.footer .ver{position:absolute;right:34px}
</style>
</head>
<body>
<aside class="sidebar">
  <div class="brand">
    <svg width="207" height="110" viewBox="0 0 207 110"><path d="M0 0H207V98Q120 60 0 96Z" fill="#fff"/><path d="M0 96Q100 60 207 98" stroke="#2b4a7a" stroke-width="7" fill="none"/></svg>
    <div class="brand-name"><i></i>Keystead</div>
  </div>
  <ul class="menu">
    <li><svg viewBox="0 0 12 12"><path d="M6 1a5 5 0 0 0-5 5v3h10V6a5 5 0 0 0-5-5z"/></svg>Dashboard</li>
    <li><svg viewBox="0 0 12 12"><circle cx="6" cy="3.5" r="2.5"/><path d="M1 11a5 4 0 0 1 10 0z"/></svg>Customers</li>
    <li><svg viewBox="0 0 12 12"><rect x="2" y="0" width="8" height="12"/></svg>Properties</li>
    <li><svg viewBox="0 0 12 12"><circle cx="4" cy="4" r="3"/><rect x="5" y="5" width="6" height="2" transform="rotate(45 6 6)"/></svg>Tenants</li>
    <li><svg viewBox="0 0 12 12"><path d="M1 8a5 5 0 0 1 10 0h-2a3 3 0 0 0-6 0z"/></svg>Contacts</li>
    <li><svg viewBox="0 0 12 12"><rect x="0" y="3" width="12" height="6" rx="3"/></svg>Contractors</li>
    <li><svg viewBox="0 0 12 12"><circle cx="3" cy="4" r="2"/><circle cx="9" cy="4" r="2"/><circle cx="6" cy="7" r="2.5"/></svg>Employees</li>
    <li><svg viewBox="0 0 12 12"><path d="M2 0h6l2 2v10H2z"/></svg>Compilance Management</li>
    <li><svg viewBox="0 0 12 12"><circle cx="6" cy="6" r="5"/></svg>Prevent.Maintenance</li>
    <li><svg viewBox="0 0 12 12"><rect y="1" width="12" height="2.5"/><rect y="5" width="12" height="2.5"/><rect y="9" width="12" height="2.5"/></svg>Work Orders</li>
    <li><svg viewBox="0 0 12 12"><path d="M0 0h6l6 6-6 6-6-6z"/></svg>Purchase Orders</li>
    <li><svg viewBox="0 0 12 12"><circle cx="5" cy="5" r="3.5" fill="none" stroke="#fff" stroke-width="2"/><rect x="8" y="7" width="2" height="5" transform="rotate(-45 9 9)"/></svg>Property Inspections</li>
    <li><svg viewBox="0 0 12 12"><circle cx="6" cy="4.5" r="4"/><rect x="4" y="9" width="4" height="3"/></svg>Energy Management</li>
    <li><svg viewBox="0 0 12 12"><rect y="1" width="12" height="8"/><rect x="3" y="10" width="6" height="2"/></svg>Risk Management</li>
    <li><svg viewBox="0 0 12 12"><rect x="2" y="2" width="8" height="6"/><rect y="9" width="12" height="2"/></svg>Project Management</li>
    <li><svg viewBox="0 0 12 12"><path d="M0 11l4-5 3 3 5-7" stroke="#fff" stroke-width="1.6" fill="none"/></svg>Financial Budgeting</li>
    <li><svg viewBox="0 0 12 12"><circle cx="6" cy="6" r="5.5"/></svg>Tenant Requests</li>
    <li><svg viewBox="0 0 12 12"><rect x="0" y="3" width="7" height="9"/><rect x="5" y="0" width="7" height="9"/></svg>Reports</li>
    <li><svg viewBox="0 0 12 12"><ellipse cx="6" cy="6" rx="6" ry="4"/></svg>Visual Reports</li>
    <li><svg viewBox="0 0 12 12"><path d="M2 0h6l2 2v10H2z"/></svg>Files</li>
    <li><svg viewBox="0 0 12 12"><rect width="5" height="5"/><rect x="7" width="5" height="5"/><rect y="7" width="5" height="5"/><rect x="7" y="7" width="5" height="5"/></svg>Pages</li>
    <li><svg viewBox="0 0 12 12"><rect x="5" y="0" width="2.5" height="12" transform="rotate(45 6 6)"/></svg>Configurations</li>
    <li><svg viewBox="0 0 12 12"><circle cx="4.5" cy="7" r="4"/><circle cx="10" cy="3" r="2"/></svg>Settings</li>
  </ul>
</aside>

<header class="stats">
  <div class="stat" style="left:44px"><div class="dock"><svg viewBox="0 0 18 18"><path d="M9 2l8 7h-2v7h-4v-5H7v5H3V9H1z"/></svg></div><div><b>03</b><span>Properties</span></div></div>
  <div class="stat" style="left:194px"><div class="dock"><svg viewBox="0 0 18 18"><circle cx="5" cy="6" r="2.5"/><circle cx="13" cy="6" r="2.5"/><circle cx="9" cy="9" r="3"/><path d="M3 17a6 5 0 0 1 12 0z"/></svg></div><div><b>08</b><span>Tenants</span></div></div>
  <div class="stat" style="left:327px"><div class="dock"><svg viewBox="0 0 18 18"><path d="M9 0l3 3H10v5h5V6l3 3-3 3v-2h-5v5h2l-3 3-3-3h2v-5H3v2L0 9l3-3v2h5V3H6z"/></svg></div><div><b>422,000.00sq.ft</b><span>Total Properties Area</span></div></div>
  <div class="stat" style="left:544px"><div class="dock"><svg viewBox="0 0 18 18"><path d="M1 1h6L5 3l3 3-2 2-3-3-2 2zM17 1v6l-2-2-3 3-2-2 3-3-2-2zM1 17v-6l2 2 3-3 2 2-3 3 2 2zM17 17h-6l2-2-3-3 2-2 3 3 2-2z"/></svg></div><div><b>233,500.00sq.ft</b><span>Rented Area</span></div></div>
  <div class="stat" style="left:759px"><div class="dock"><svg viewBox="0 0 18 18"><path d="M9 0l3 3H10v5h5V6l3 3-3 3v-2h-5v5h2l-3 3-3-3h2v-5H3v2L0 9l3-3v2h5V3H6z"/></svg></div><div><b>188,500.00sq.ft</b><span>Vacancies Area</span></div></div>
</header>

<main class="card">
  <h1 class="title">Active <em>Dashboard</em></h1>
  <nav class="ranges"><span class="on">Last 7 Days</span><span>Last Months</span><span>Last 3 Months</span><span>Next 7 Days</span><span>Next Months</span><span>Mext 3 Months</span></nav>
  <div class="period"><svg viewBox="0 0 18 14" fill="#fff"><rect x="0" y="0" width="1.5" height="14"/><rect x="0" y="12.5" width="18" height="1.5"/><rect x="4" y="6" width="1.5" height="5"/><rect x="7" y="3" width="1.5" height="8"/><rect x="10" y="5" width="1.5" height="6"/><rect x="13" y="2" width="1.5" height="9"/></svg>12/27/2020 - 01/03/2021</div>
  <svg class="chart" viewBox="230 136 946 832">
    <g stroke="#e3e6ea" stroke-width="1">
      <line x1="341" y1="342" x2="1144" y2="342"/><line x1="341" y1="425" x2="1144" y2="425"/><line x1="341" y1="507" x2="1144" y2="507"/><line x1="341" y1="590" x2="1144" y2="590"/><line x1="341" y1="672" x2="1144" y2="672"/>
    </g>
    <line x1="341" y1="323" x2="341" y2="758" stroke="#ccd0d6"/>
    <line x1="341" y1="758" x2="1144" y2="758" stroke="#ccd0d6"/>
    <g fill="#5f6b7a"><rect x="255" y="338" width="13" height="2"/><rect x="255" y="343" width="13" height="2"/><rect x="255" y="348" width="13" height="2"/></g>
    <text x="262" y="542" transform="rotate(-90 262 542)" text-anchor="middle" font-size="12" font-weight="700" fill="#4f6077" dominant-baseline="middle">NUMBER</text>
    <g font-size="12" fill="#5f6b7a">
      <text x="291" y="347">1.25</text><text x="291" y="430">1</text><text x="291" y="512">0.75</text><text x="291" y="595">0.5</text><text x="291" y="677">0.25</text><text x="291" y="759">0</text>
    </g>
    <g font-size="12.5" fill="#5f6b7a" text-anchor="middle">
      <text x="375" y="797">12/27/20</text><text x="480" y="797">12/28/20</text><text x="585" y="797">12/29/20</text><text x="689" y="797">12/30/20</text><text x="794" y="797">12/31/20</text><text x="898" y="797">01/01/21</text><text x="1004" y="797">02/01/21</text><text x="1109" y="797">03/01/21</text>
    </g>
    <g fill="#0a7cff">
      <rect x="578.5" y="670" width="13" height="88"/><rect x="682.5" y="590" width="13" height="168"/><rect x="787.5" y="608" width="13" height="150"/><rect x="891.5" y="642" width="13" height="116"/>
    </g>
    <g fill="#fff" stroke="#0a7cff" stroke-width="2.5">
      <circle cx="585" cy="670" r="10"/><circle cx="689" cy="590" r="10"/><circle cx="794" cy="608" r="10"/><circle cx="898" cy="642" r="10"/>
    </g>
  </svg>
  <div class="legend">
    <span><i style="background:#0a7cff"></i>Scheduled Maintenance</span>
    <span><i style="background:#5fd34a"></i>Completed Scheduled Maintenance</span>
    <span><i style="background:#f2c94c"></i>Future Scheduled Maintenance</span>
    <span><i style="background:#4f6077"></i>Scheduled Work Orders</span>
    <span><i style="background:#a259e6"></i>Completed Work Orders</span>
    <span><i style="background:#f06bb4"></i>Property Inspections in Progress</span>
    <span><i style="background:#e0a850"></i>Completed Property Inspections</span>
  </div>
</main>

<footer class="footer">© 2021 ERP software. All rights reserved.Privacy Terms of Use<span class="ver">C9</span></footer>
</body>
</html>
```